The Copper Kite Website Redesign

I want a new design and website for www.thecopperkitebrookvale.com where part of the home page includes our daily specials from our POS Toast to be pulled from API. I have included photos and links to give you a better feel for the style of our restaurant.

Coding

Coded - Design and coding required

```html
<!DOCTYPE html>
<html lang="en">
<head>
<meta charset="utf-8">
<title>The Copper Kite – Restaurant</title>
<link href="https://fonts.googleapis.com/css2?family=Inter:wght@400;500;600;700&family=Mouse+Memoirs&family=Kaushan+Script&family=Yellowtail&display=swap" rel="stylesheet">
<style>
:root{
  --black:#000;
  --dark:#111;
  --panel:#1a1a1a;
  --white:#fff;
  --orange:#ff5a00;
  --amber:#ff8a00;
  --yellow:#ffd400;
  --grey:#cfcfcf;
  --line:#5a5a5a;
}
*{margin:0;padding:0;box-sizing:border-box}
html,body{width:1200px;height:3772px;overflow:hidden;background:var(--black);color:var(--white);font-family:"Inter",sans-serif}
.page{position:relative;width:1200px;height:3772px}
.abs{position:absolute}
.display{font-family:"Mouse Memoirs",sans-serif;font-weight:400;line-height:1}
.btn{position:absolute;background:var(--orange);color:var(--white);font-weight:700;font-size:14px;border-radius:6px;display:flex;align-items:center;justify-content:center;letter-spacing:.2px}

/* top bar + header */
.topbar{left:0;top:0;width:1200px;height:40px;background:var(--black);font-size:12px;font-weight:600;display:flex;align-items:center;justify-content:center;z-index:5}
.hero{left:0;top:40px;width:1200px;height:565px;background:var(--black)}
.hero-photo{position:absolute;left:492px;top:0;width:708px;height:565px;background:radial-gradient(circle at 60% 65%,#8a5a25 0%,#5b3515 30%,#2a1a10 60%,#140e0b 100%)}
.nav{position:absolute;top:35px;display:flex;gap:26px;font-size:13px;font-weight:500}
.nav-left{left:290px}
.nav-right{left:714px}
.nav-rule{position:absolute;top:71px;height:2px;background:#8a8a8a}
.nav-active{position:absolute;left:290px;top:69px;width:42px;height:4px;background:var(--amber)}
.brand-disc{position:absolute;left:512px;top:-50px;width:176px;height:176px;border-radius:50%;background:var(--black);display:flex;align-items:center;justify-content:center;padding-top:40px}
.brand-name{font-family:"Mouse Memoirs",sans-serif;font-size:30px;color:var(--white);text-align:center;line-height:1}
.cart-badge{position:absolute;left:1044px;top:27px;width:14px;height:14px;border-radius:50%;background:var(--yellow);color:#000;font-size:9px;display:flex;align-items:center;justify-content:center}
.hero-title{left:180px;top:160px;font-size:120px;letter-spacing:-1px}
.hero-sub{left:256px;top:268px;font-family:"Kaushan Script",cursive;font-size:60px;color:var(--amber)}
.arrow-btn{position:absolute;top:476px;width:38px;height:38px;border-radius:50%;background:var(--white);display:flex;align-items:center;justify-content:center}

/* about */
.about{left:0;top:605px;width:1200px;height:680px;background:linear-gradient(180deg,#1d1d1d 0%,#111 60%,#1a1612 100%)}
.about-frame{left:155px;top:140px;width:450px;height:415px}
.about-title{left:622px;top:90px;font-size:74px}
.about-copy{left:622px;top:172px;width:434px;font-size:14.5px;line-height:24px;text-align:justify}
.about-copy p+p{margin-top:24px}

/* foods */
.foods{left:0;top:1285px;width:1200px;height:947px;background:var(--black)}
.section-title{width:1200px;text-align:center;font-size:74px}
.food-card{position:absolute;width:270px;text-align:center}
.food-ring{width:270px;height:270px;border-radius:50%;padding:4px;background:conic-gradient(var(--orange),var(--yellow),var(--orange),var(--yellow),var(--orange))}
.food-ring .inner{width:100%;height:100%;border-radius:50%;background:var(--black);padding:10px}
.food-photo{width:100%;height:100%;border-radius:50%;position:relative}
.food-label{margin-top:26px;font-size:20px;font-weight:500}
.food-label.active{color:var(--amber)}

/* offer + tagline */
.offer{left:0;top:2232px;width:1200px;height:460px;background:linear-gradient(90deg,#0d0a08 0%,#1f140c 40%,#3a2615 70%,#24170d 100%)}
.offer-line{width:420px;text-align:center;left:225px;font-size:72px;color:var(--white)}
.offer-deal{left:268px;top:250px;font-family:"Kaushan Script",cursive;font-size:88px;color:var(--amber)}
.tagline{left:0;top:2692px;width:1200px;height:202px;background:linear-gradient(90deg,var(--orange) 0%,var(--amber) 50%,var(--yellow) 100%);overflow:hidden}
.tagline-text{position:absolute;width:1200px;top:55px;text-align:center;font-family:"Yellowtail",cursive;font-size:70px}

/* specials */
.specials{left:0;top:2894px;width:1200px;height:552px;background:var(--black)}
.special-card{position:absolute;top:195px;width:286px;height:251px;border-radius:10px}
.plus-btn{position:absolute;left:873px;top:417px;width:80px;height:80px;border-radius:50%;background:var(--white);color:#111;font-size:34px;display:flex;align-items:center;justify-content:center;box-shadow:0 4px 14px rgba(0,0,0,.5)}

/* footer */
.footer{left:0;top:3446px;width:1200px;height:326px;background:linear-gradient(180deg,#161616,#0c0c0c)}
.footer-logo{left:210px;top:82px;width:122px;height:122px;border-radius:50%;background:var(--white);display:flex;align-items:center;justify-content:center}
.footer-logo span{font-family:"Mouse Memoirs",sans-serif;color:#111;font-size:26px;text-align:center;line-height:1}
.vrule{position:absolute;top:90px;width:1px;height:120px;background:var(--line)}
.footer h3{font-size:18px;font-weight:700;position:absolute}
.contact-row{position:absolute;left:458px;display:flex;gap:12px;font-size:15px;line-height:22px}
.email-field{left:759px;top:129px;width:238px;height:36px;border:1px solid #aaa;border-radius:18px;font-size:11px;display:flex;align-items:center;padding-left:18px}
.social{position:absolute;top:258px;display:flex;gap:6px;left:209px}
.social span{width:28px;height:28px;border-radius:50%;border:1.5px solid #bbb;background:#1c1c1c}
.social span.on{background:var(--orange);border-color:var(--orange)}
.copyright{left:746px;top:265px;font-size:15px}
</style>
</head>
<body>
<div class="page">

  <div class="abs topbar">LOREM IPSUM DOLOR SIT AMET, CONSECTETUR ADIPISCING ELIT, SED DO EIUSMOD</div>

  <section class="abs hero">
    <div class="hero-photo" role="img" aria-label="Plated waffles with berries and powdered sugar beside a syrup jug"></div>
    <nav class="nav nav-left"><span>HOME</span><span>ABOUT</span><span>MENUS</span></nav>
    <div class="nav-rule" style="left:144px;width:340px"></div>
    <div class="nav-active"></div>
    <nav class="nav nav-right"><span>PORTFOLIO</span><span>BLOG</span><span>CONTACT</span></nav>
    <div class="nav-rule" style="left:715px;width:340px"></div>
    <svg class="abs" style="left:995px;top:37px" width="14" height="14" viewBox="0 0 14 14"><circle cx="6" cy="6" r="4.2" fill="none" stroke="#fff" stroke-width="2"/><line x1="9" y1="9" x2="13" y2="13" stroke="#fff" stroke-width="2"/></svg>
    <svg class="abs" style="left:1036px;top:36px" width="16" height="14" viewBox="0 0 16 14"><path d="M1 1h3l2 8h8l1.5-6H5" fill="none" stroke="#fff" stroke-width="1.8"/><circle cx="7" cy="12" r="1.3" fill="#fff"/><circle cx="13" cy="12" r="1.3" fill="#fff"/></svg>
    <div class="cart-badge">0</div>
    <div class="brand-disc"><span class="brand-name">The Copper<br>Kite</span></div>
    <div class="abs display hero-title">The Copper Kite</div>
    <div class="abs hero-sub">Restaurant</div>
    <div class="btn" style="left:324px;top:338px;width:153px;height:46px">BOOK NOW</div>
    <div class="arrow-btn" style="left:357px"><svg width="10" height="12"><path d="M7 1 2 6l5 5" fill="none" stroke="#222" stroke-width="1.8"/></svg></div>
    <div class="arrow-btn" style="left:405px"><svg width="10" height="12"><path d="M3 1l5 5-5 5" fill="none" stroke="#222" stroke-width="1.8"/></svg></div>
  </section>

  <section class="abs about">
    <svg class="abs about-frame" viewBox="0 0 450 415" role="img" aria-label="Burger with cheese and lettuce in a bar setting, in a tilted frame">
      <defs><linearGradient id="burgerTone" x1="0" y1="0" x2="0" y2="1"><stop offset="0" stop-color="#5a6b7a"/><stop offset=".45" stop-color="#b57a3a"/><stop offset=".75" stop-color="#4a2d18"/><stop offset="1" stop-color="#6d8a3a"/></linearGradient></defs>
      <polygon points="20,360 60,390 110,385 90,120" fill="var(--orange)"/>
      <polygon points="380,20 455,35 420,170 360,150" fill="var(--yellow)"/>
      <polygon points="0,0 420,25 400,410 25,385" fill="#e8e8e8"/>
      <polygon points="10,8 410,33 392,400 32,376" fill="url(#burgerTone)"/>
    </svg>
    <div class="abs display about-title">About Us</div>
    <div class="abs about-copy">
      <p>Lorem ipsum dolor sit amet, consectetur adipiscing elit, sed do eiusmod tempor incididunt ut labore et dolore magna aliqua. Ut enim ad minim veniam, quis nostrud exercitation ullamco laboris nisi ut aliquip ex ea commodo consequat. Duis aute irure dolor in reprehenderit in voluptate velit esse cillum dolore eu fugiat nulla pariatur. Excepteur sint occaecat cupidatat non proident, sunt in culpa qui officia deserunt mollit anim id est laborum.</p>
      <p>Lorem ipsum dolor sit amet, consectetur adipiscing elit, sed do eiusmod tempor incididunt ut labore et dolore magna aliqua. Ut enim ad minim veniam, quis nostrud exercitation ullamco laboris nisi ut aliquip ex ea commodo</p>
    </div>
    <div class="btn" style="left:622px;top:502px;width:153px;height:46px">READ MORE</div>
  </section>

  <section class="abs foods">
    <div class="abs display section-title" style="top:82px">Our Foods</div>
    <div class="food-card" style="left:161px;top:172px"><div class="food-ring"><div class="inner"><div class="food-photo" role="img" aria-label="Cheeseburger with bacon and tomato" style="background:radial-gradient(circle,#b87a3a,#4a3020 60%,#2a2a2a)"></div></div></div><div class="food-label">Lorem ipsum dolor</div></div>
    <div class="food-card" style="left:465px;top:172px"><div class="food-ring"><div class="inner"><div class="food-photo" role="img" aria-label="Salad bowl with greens and tomatoes" style="background:radial-gradient(circle,#4a5a2a,#2a2218 60%,#141414)"><div class="btn" style="left:45px;top:108px;width:150px;height:44px">TASTE NOW</div></div></div></div><div class="food-label active">Lorem ipsum dolor</div></div>
    <div class="food-card" style="left:769px;top:172px"><div class="food-ring"><div class="inner"><div class="food-photo" role="img" aria-label="Cocktails with lime and orange" style="background:radial-gradient(circle,#c8a060,#6a6a5a 50%,#2e2e2e)"></div></div></div><div class="food-label">Lorem ipsum dolor</div></div>
    <div class="food-card" style="left:161px;top:516px"><div class="food-ring"><div class="inner"><div class="food-photo" role="img" aria-label="Row of colourful fruit drinks" style="background:radial-gradient(circle,#c8d060,#b05050 55%,#202020)"></div></div></div><div class="food-label">Lorem ipsum dolor</div></div>
    <div class="food-card" style="left:465px;top:516px"><div class="food-ring"><div class="inner"><div class="food-photo" role="img" aria-label="Tacos with meat and fresh toppings" style="background:radial-gradient(circle,#a87a40,#4a3a28 60%,#1e1e1e)"></div></div></div><div class="food-label">Lorem ipsum dolor</div></div>
    <div class="food-card" style="left:769px;top:516px"><div class="food-ring"><div class="inner"><div class="food-photo" role="img" aria-label="Steak fajita wrap with peppers" style="background:radial-gradient(circle,#c89a58,#6a4a30 60%,#3a3a3a)"></div></div></div><div class="food-label">Lorem ipsum dolor</div></div>
  </section>

  <section class="abs offer" role="img" aria-label="Dim bar interior with stools and bottle shelves">
    <div class="abs display offer-line" style="top:80px">Get A Offer For</div>
    <div class="abs display offer-line" style="top:168px">Pre-Booking</div>
    <div class="abs offer-deal">50%-Offer</div>
  </section>

  <section class="abs tagline">
    <svg class="abs" style="left:0;top:0" width="1200" height="202"><circle cx="140" cy="0" r="90" fill="#ff7000" opacity=".5"/><circle cx="1040" cy="210" r="90" fill="#ffb000" opacity=".7"/></svg>
    <div class="tagline-text">For the love of delicious food.</div>
  </section>

  <section class="abs specials">
    <div class="abs display section-title" style="top:90px">Our Daily Specials</div>
    <div class="special-card" style="left:143px;background:linear-gradient(135deg,#6a3818,#a05a28,#3a2010)" role="img" aria-label="Roasted sweet potato cubes"></div>
    <div class="special-card" style="left:457px;background:linear-gradient(135deg,#b01a1a,#e8e8e0 40%,#4a8a2a 80%)" role="img" aria-label="Plate with salsa and jalapeño peppers"></div>
    <div class="special-card" style="left:771px;background:linear-gradient(135deg,#c8a040,#e8c860 50%,#3a4a2a)" role="img" aria-label="Scrambled eggs with spinach"></div>
    <div class="plus-btn">+</div>
  </section>

  <footer class="abs footer">
    <div class="abs footer-logo"><span>The Copper<br>Kite</span></div>
    <div class="vrule" style="left:398px"></div>
    <div class="vrule" style="left:702px"></div>
    <h3 style="left:458px;top:92px">Stay In Touch</h3>
    <div class="contact-row" style="top:128px">
      <svg width="28" height="28" viewBox="0 0 24 24"><path d="M6 3l3 4-2 2c1 3 4 6 7 7l2-2 4 3-2 3C10 20 4 14 3 6z" fill="none" stroke="var(--orange)" stroke-width="1.5"/></svg>
      <div>Phone :<br>(555) 218-4730</div>
    </div>
    <div class="contact-row" style="top:188px">
      <svg width="28" height="22" viewBox="0 0 28 22"><rect x="1" y="2" width="26" height="18" fill="none" stroke="var(--orange)" stroke-width="1.5"/><path d="M1 2l13 10L27 2" fill="none" stroke="var(--orange)" stroke-width="1.5"/></svg>
      <div>Email :<br>eat@thecopperkitebrookvale.com</div>
    </div>
    <h3 style="left:759px;top:92px">Subscribe To Our Newsletter</h3>
    <div class="abs email-field">Email address</div>
    <div class="btn" style="left:759px;top:178px;width:110px;height:34px;border-radius:17px;font-size:11px">SUBSCRIBE</div>
    <div class="social" aria-label="Social links"><span></span><span class="on"></span><span></span><span></span></div>
    <div class="abs copyright">Copyrights © 2025. All Rights Reserved.</div>
  </footer>

</div>
</body>
</html>
```